Business card design needed

This is a new business and a unique service.
The market is academic staff at universities in Australia.
The services include workshops, seminars, individual research planning, individual support to develop grant applications for major funding. I will travel to work with people or work electronically with individuals. I have a highly successful track record and am known in many universities for work done in the past.

Target Market(s)

university professorial staff and junior academic staff in australia

Industry/Entity Type

Travel

Contact Information for Business Card

The Scholar Summit
Charting Routes to Study Grants

Dr Helen T Brisk

www.scholarsummit.com.au
E: info@scholarsummit.com.au
Ph: 0438 602741

Requirements
Must have
• I want a classic simple design. Colours - clean shades of blue with a contrast (not browns or orange).
I want to see line used as the primary feature, diagonal or other acute angles through part of the card.
Fonts should be crisp, angular and highly readable. Use upper and lower case in all text (except email and web address)
A simple logo based on TSS would be good.
Card can be designed vertically if the design works best that way.

```html
<!DOCTYPE html>
<html lang="en">
<head>
<meta charset="utf-8">
<title>The Scholar Summit – Business Cards</title>
<link href="https://fonts.googleapis.com/css2?family=Source+Sans+3:wght@400;600;700&display=swap" rel="stylesheet">
<style>
  :root {
    --stage: #e6e8eb;
    --card: #f4f5f6;
    --card-edge: #dcdfe2;
    --navy: #0f4c81;
    --blue: #1f6fb2;
    --sky: #8fb9dd;
    --ink: #1d1f22;
    --faint: #c9cdd1;
  }
  * { margin: 0; padding: 0; box-sizing: border-box; }
  html, body {
    width: 1200px; height: 900px; overflow: hidden;
    background: var(--stage);
    font-family: "Source Sans 3", "Myriad Pro", sans-serif;
    color: var(--ink);
  }
  .card-set {
    position: absolute; inset: 0;
    display: flex; align-items: center; justify-content: center; gap: 60px;
  }
  .card {
    position: relative;
    width: 520px; height: 318px;
    background: linear-gradient(135deg, #fafbfb 0%, var(--card) 55%, #e9ebed 100%);
    border: 1px solid var(--card-edge);
    box-shadow: 0 6px 18px rgba(0,0,0,0.12);
    overflow: hidden;
  }
  .card__bands { position: absolute; inset: 0; width: 100%; height: 100%; }
  .brand {
    position: absolute;
    display: flex; align-items: center; gap: 10px;
  }
  .brand__mark {
    width: 14px; height: 14px; background: var(--blue);
  }
  .brand__name {
    font-weight: 700; font-size: 24px; color: var(--navy); letter-spacing: 0.2px;
  }
  .card--front .brand { left: 40px; top: 128px; }
  .tagline {
    position: absolute; left: 262px; top: 166px;
    font-size: 15px; font-weight: 600; color: var(--ink);
  }
  .web-address {
    position: absolute; left: 178px; top: 222px;
    font-size: 12px; color: var(--faint); letter-spacing: 0.3px;
  }
  .card--contact .brand { left: 40px; top: 110px; }
  .contact {
    position: absolute; right: 34px; bottom: 44px; text-align: right;
  }
  .contact__name { font-size: 19px; margin-bottom: 6px; }
  .contact__lines { font-size: 15px; }
  .contact__label { font-weight: 700; }
</style>
</head>
<body>
  <main class="card-set">
    <section class="card card--front">
      <svg class="card__bands" viewBox="0 0 520 318" preserveAspectRatio="none" aria-hidden="true">
        <defs>
          <linearGradient id="front-band" x1="0" x2="1" y1="0" y2="0">
            <stop offset="0" stop-color="#1f6fb2" stop-opacity="0"/>
            <stop offset="0.5" stop-color="#1f6fb2" stop-opacity="0.7"/>
            <stop offset="1" stop-color="#0f4c81"/>
          </linearGradient>
          <linearGradient id="front-glow" x1="0" x2="1" y1="0" y2="0">
            <stop offset="0" stop-color="#8fb9dd" stop-opacity="0"/>
            <stop offset="1" stop-color="#8fb9dd" stop-opacity="0.8"/>
          </linearGradient>
        </defs>
        <polygon points="0,260 520,278 520,318 360,318" fill="url(#front-glow)"/>
        <polygon points="0,256 520,286 520,300" fill="url(#front-band)"/>
      </svg>
      <div class="brand">
        <span class="brand__mark"></span>
        <span class="brand__name">The Scholar Summit</span>
      </div>
      <p class="tagline">Charting Routes to Study Grants</p>
      <p class="web-address">www.scholarsummit.com.au</p>
    </section>

    <section class="card card--contact">
      <svg class="card__bands" viewBox="0 0 520 318" preserveAspectRatio="none" aria-hidden="true">
        <defs>
          <linearGradient id="top-band" x1="0" x2="1" y1="0" y2="0">
            <stop offset="0" stop-color="#1f6fb2" stop-opacity="0"/>
            <stop offset="0.45" stop-color="#1f6fb2" stop-opacity="0.75"/>
            <stop offset="1" stop-color="#0f4c81"/>
          </linearGradient>
          <linearGradient id="top-glow" x1="0" x2="1" y1="0" y2="0">
            <stop offset="0" stop-color="#8fb9dd" stop-opacity="0"/>
            <stop offset="1" stop-color="#8fb9dd" stop-opacity="0.7"/>
          </linearGradient>
        </defs>
        <polygon points="30,46 520,0 520,22 150,58" fill="url(#top-glow)"/>
        <polygon points="20,40 520,0 520,14" fill="url(#top-band)"/>
      </svg>
      <div class="brand">
        <span class="brand__mark"></span>
        <span class="brand__name">The Scholar Summit</span>
      </div>
      <div class="contact">
        <p class="contact__name">Dr Helen T Brisk</p>
        <p class="contact__lines"><span class="contact__label">P:</span> 0438 602741 | <span class="contact__label">E:</span> info@scholarsummit.com.au</p>
      </div>
    </section>
  </main>
</body>
</html>
```